Business Card Design for Technology Company

New business card design needed for technology company director.
Ideally, the design will fit the style and nature of the industry. We are a supplier of quality products and services, and we hope the design will give customers and suppliers this impression.

Target Market(s)

3D Printing Industry

Industry/Entity Type

Technology Equipment

Contact Information for Business Card

Name: Marcus Lin
Title: Director
Company address: Factory K4, 7B Harlowe Road, Springvale Victoria Australia 3150
Telephone: +61-3-8555 6413
Email: marcus.lin@vortalmake.com.au
Website: www.vortalmake.com.au

Requirements
Must have
• All information in business card details
• Company logo
• '3D Printers and 3D Print Filaments' at proper place
Nice to have
• Style to fit the industry
• Colour to fit logo

```html
<!DOCTYPE html>
<html lang="en">
<head>
<meta charset="utf-8">
<title>Vortal Make – Business Card</title>
<link rel="stylesheet" href="https://fonts.googleapis.com/css2?family=Lato:wght@400;700;900&family=Orbitron:wght@500&display=swap">
<style>
  :root {
    --bg: #3a3a3a;
    --card-front: #ffffff;
    --card-back: #efefef;
    --ink: #111111;
    --brand-blue: #1584c9;
    --brand-orange: #f7961d;
    --shadow: rgba(0,0,0,0.45);
  }
  * { margin: 0; padding: 0; box-sizing: border-box; }
  html, body { width: 1200px; height: 802px; overflow: hidden; }
  body {
    background: var(--bg);
    position: relative;
    font-family: "Lato", sans-serif;
    color: var(--ink);
  }
  .card {
    position: absolute;
    top: 274px;
    width: 443px;
    height: 265px;
    box-shadow: 0 3px 8px var(--shadow);
    overflow: hidden;
  }
  .card--front { left: 136px; background: var(--card-front); }
  .card--back { left: 624px; background: var(--card-back); }

  .brand-block {
    position: absolute;
    left: 5px; top: 5px;
    width: 230px; height: 255px;
    display: flex;
    flex-direction: column;
    align-items: center;
    justify-content: center;
    gap: 12px;
  }
  .brand-square {
    width: 70px; height: 70px;
    background: var(--brand-blue);
    flex: none;
  }
  .brand-name {
    font-family: "Lato", sans-serif;
    font-weight: 900;
    font-size: 21px;
    letter-spacing: 3px;
    color: var(--ink);
    white-space: nowrap;
  }
  .tagline {
    font-family: "Lato", sans-serif;
    font-weight: 700;
    font-size: 8.5px;
    letter-spacing: 1.4px;
    text-transform: uppercase;
    color: var(--ink);
    white-space: nowrap;
  }

  .identity {
    position: absolute;
    right: 26px; top: 38px;
    text-align: right;
  }
  .identity__name {
    font-family: "Orbitron", sans-serif;
    font-weight: 500;
    font-size: 15.5px;
    letter-spacing: 0.5px;
    line-height: 1.1;
  }
  .identity__title { font-size: 12.5px; line-height: 1.2; }

  .address {
    position: absolute;
    right: 26px; top: 114px;
    text-align: right;
    font-size: 12.5px;
    line-height: 16px;
    font-style: normal;
  }
  .contacts {
    position: absolute;
    right: 26px; top: 195px;
    list-style: none;
    text-align: right;
    font-size: 12.5px;
    line-height: 16px;
  }
  .contacts li { display: flex; justify-content: flex-end; align-items: center; gap: 2px; white-space: nowrap; }
  .contacts svg { width: 10px; height: 10px; fill: var(--ink); }

  .back-brand {
    position: absolute;
    left: 66px; top: 99px;
    display: flex;
    align-items: center;
    gap: 22px;
  }
  .back-brand .brand-square {
    width: 66px; height: 66px;
    background: var(--brand-orange);
  }
  .back-brand__text {
    display: flex;
    flex-direction: column;
    gap: 6px;
  }
  .back-brand .brand-name { font-size: 30px; letter-spacing: 3px; line-height: 1; }
</style>
</head>
<body>
  <section class="card card--front">
    <div class="brand-block">
      <span class="brand-square"></span>
      <span class="brand-name">VORTAL MAKE</span>
      <span class="tagline">3D Printers and 3D Print Filaments</span>
    </div>

    <div class="identity">
      <div class="identity__name">MARCUS LIN</div>
      <div class="identity__title">Director</div>
    </div>

    <address class="address">
      Factory K4<br>
      7B Harlowe Road<br>
      Springvale Victoria<br>
      Australia 3150
    </address>

    <ul class="contacts">
      <li>+61-3-8555 6413
        <svg viewBox="0 0 10 10" aria-hidden="true"><path d="M1 4 Q5 0 9 4 L8 5 L6.5 4 L6.5 3.3 Q5 2.8 3.5 3.3 L3.5 4 L2 5 Z M2.5 5.5 L7.5 5.5 L8.5 9 L1.5 9 Z"/></svg>
      </li>
      <li>marcus.lin@vortalmake.com.au
        <svg viewBox="0 0 10 10" aria-hidden="true"><path d="M1 2 H9 V8 H1 Z M1.6 2.6 L5 5.3 L8.4 2.6 Z" fill-rule="evenodd"/></svg>
      </li>
      <li>www.vortalmake.com.au
        <svg viewBox="0 0 10 10" aria-hidden="true"><circle cx="5" cy="5" r="4.3"/></svg>
      </li>
    </ul>
  </section>

  <section class="card card--back">
    <div class="back-brand">
      <span class="brand-square"></span>
      <div class="back-brand__text">
        <span class="brand-name">VORTAL MAKE</span>
        <span class="tagline">3D Printers and 3D Print Filaments</span>
      </div>
    </div>
  </section>
</body>
</html>
```